Business card design for Automotive workshop

We need a business card for a new automotive repair and tyre shop called Keelstone Prime Automotive located in New Zealand. We are a clean, modern and fresh workshop and company.

Front needs to feature logo,
my name:
Marlo Fenwicke (director)

Address:
48 Tarn Lane
Whitianga 3510

Phone: 07 594 2713
Mobile: 027 451 9362
Email: office@keelstoneautomotive.example.nz
Website: keelstoneautomotive.example.nz

Back needs to feature an area to write down appointment details, date and time.

Also feature a list of jobs and work we do such as,
Vehicle Servicing
All Mechanical Repairs
Warrant of Fitness
Tyres & Wheel Alignments
Automotive Diagnostics
Automotive Parts & Supplies

```html
<!DOCTYPE html>
<html lang="en">
<head>
<meta charset="utf-8">
<title>Keelstone Prime Automotive – Business Card</title>
<link href="https://fonts.googleapis.com/css2?family=Noto+Sans:wght@400;600;700&display=swap" rel="stylesheet">
<style>
  :root {
    --bg: #2e2e2e;
    --card: #050505;
    --red: #e3262b;
    --white: #ffffff;
    --text: #f2f2f2;
    --art-a: rgba(70, 32, 26, 0.85);
    --art-b: rgba(45, 20, 16, 0.0);
  }
  * { margin: 0; padding: 0; box-sizing: border-box; }
  html, body { width: 1200px; height: 750px; overflow: hidden; }
  body {
    background: var(--bg);
    font-family: "Noto Sans", sans-serif;
    color: var(--text);
    position: relative;
  }
  .card {
    position: absolute;
    top: 187px;
    height: 328px;
    background: var(--card);
    border-radius: 18px;
    overflow: hidden;
    box-shadow: 0 4px 10px rgba(0,0,0,0.5);
  }
  .card--front { left: 38px; width: 558px; }
  .card--back { left: 610px; width: 562px; }

  .card__art {
    position: absolute;
    background: radial-gradient(ellipse at 40% 60%, var(--art-a) 0%, rgba(55,25,20,0.45) 45%, var(--art-b) 75%);
  }
  .card--front .card__art { left: 266px; top: 14px; width: 300px; height: 210px; }
  .card--back .card__art { left: 222px; top: 17px; width: 345px; height: 210px; }

  .brand {
    position: absolute;
    color: var(--red);
    font-weight: 700;
    text-transform: uppercase;
    line-height: 1.05;
    letter-spacing: 0.04em;
  }
  .card--front .brand { left: 30px; top: 30px; font-size: 17px; }
  .card--back .brand { left: 0; right: 0; top: 50px; text-align: center; font-size: 25px; }

  .person { position: absolute; left: 30px; top: 98px; }
  .person__name { color: var(--red); font-weight: 700; font-size: 17.5px; letter-spacing: 0.02em; line-height: 1.1; }
  .person__role { font-size: 13px; line-height: 1.4; }

  .contact { position: absolute; left: 30px; top: 185px; list-style: none; }
  .contact__item { display: flex; align-items: center; height: 20px; font-size: 14.5px; line-height: 1; }
  .contact__icon { width: 12px; height: 12px; margin-right: 6px; fill: var(--red); flex: none; }

  .services { position: absolute; left: 59px; top: 139px; list-style: none; }
  .services__item { display: flex; align-items: center; height: 26.8px; font-size: 11.5px; letter-spacing: 0.02em; }
  .services__item::before {
    content: ""; width: 4px; height: 4px; border-radius: 50%;
    background: var(--red); margin-right: 3px;
  }

  .appointment { position: absolute; left: 278px; top: 231px; }
  .appointment__row { display: flex; align-items: center; height: 22px; margin-bottom: 9px; }
  .appointment__label { width: 42px; text-align: right; color: var(--red); font-size: 15.5px; margin-right: 8px; }
  .appointment__field { width: 146px; height: 22px; background: var(--white); border-radius: 11px; }
</style>
</head>
<body>

<section class="card card--front">
  <div class="card__art" role="img" aria-label="Faint car silhouette with spanner illustration"></div>
  <div class="brand">Keelstone Prime<br>Automotive</div>
  <div class="person">
    <div class="person__name">Marlo Fenwicke</div>
    <div class="person__role">Managing Director</div>
  </div>
  <ul class="contact">
    <li class="contact__item">
      <svg class="contact__icon" viewBox="0 0 12 12"><path d="M3 0h6a1 1 0 0 1 1 1v10a1 1 0 0 1-1 1H3a1 1 0 0 1-1-1V1a1 1 0 0 1 1-1zm.6 1.4v8h4.8v-8zM6 10a.6.6 0 1 0 0 1.2A.6.6 0 0 0 6 10z"/></svg>
      + 027 451 9362
    </li>
    <li class="contact__item">
      <svg class="contact__icon" viewBox="0 0 12 12"><path d="M0 4c2-3 10-3 12 0v1.5H9V4c-1.5-.8-4.5-.8-6 0v1.5H0zM3 6h6l2 5H1z"/></svg>
      + 07 594 2713
    </li>
    <li class="contact__item">
      <svg class="contact__icon" viewBox="0 0 12 12"><path d="M0 2h12v1L6 7 0 3zm0 2.3 6 4 6-4V10H0z"/></svg>
      office@keelstoneautomotive.example.nz
    </li>
    <li class="contact__item">
      <svg class="contact__icon" viewBox="0 0 12 12"><path d="M0 1h12v8H7v1.5h2V11H3v-.5h2V9H0zm1 1v6h10V2z"/></svg>
      keelstoneautomotive.example.nz
    </li>
    <li class="contact__item">
      <svg class="contact__icon" viewBox="0 0 12 12"><path d="M6 0a4 4 0 0 1 4 4c0 3-4 8-4 8S2 7 2 4a4 4 0 0 1 4-4zm0 2.4a1.6 1.6 0 1 0 0 3.2 1.6 1.6 0 0 0 0-3.2z"/></svg>
      48 Tarn Lane, Whitianga 3510
    </li>
  </ul>
</section>

<section class="card card--back">
  <div class="card__art" role="img" aria-label="Faint car silhouette with spanner illustration"></div>
  <div class="brand">Keelstone Prime<br>Automotive</div>
  <ul class="services">
    <li class="services__item">Vehicle Servicing</li>
    <li class="services__item">All Mechanical Repairs</li>
    <li class="services__item">Warrant of Fitness</li>
    <li class="services__item">Tyres &amp; Wheel Alignments</li>
    <li class="services__item">Automotive Diagnostics</li>
    <li class="services__item">Automotive Parts &amp; Supplies</li>
  </ul>
  <div class="appointment">
    <div class="appointment__row"><span class="appointment__label">Date</span><span class="appointment__field"></span></div>
    <div class="appointment__row"><span class="appointment__label">Time</span><span class="appointment__field"></span></div>
  </div>
</section>

</body>
</html>
```